Web Calculator design Housing Investment

We have a web calculator that needs to be fixed from a design perspective. The key tasks are:<br/>1. Selecting icons / pictures / colours for the various steps<br/>2. Designing navigation between calculator steps<br/>3. Making suggestions for chart design. The limitation is that the charts are all using the Vextra API (the same charts that Vextra Grids use).<br/><br/>There are four entry screens and then a result screen. See attached PDF for screenshots. You can see our website at https://larkhollowfunds.com for our corporate colours and style.

Target Market(s)

Real Estate Investors

Industry/Entity Type

Financial Planning

Number of Pages Required

1 page

Font styles to use
Sans Serif
Other font styles liked:
• Ubuntu

Colors
86cae7
3176b5
0455a3
ffffff

Requirements
Must have
• New Icons
• Suggested design for navigation
• Suggested design for charts

```html
<!DOCTYPE html>
<html lang="en">
<head>
<meta charset="utf-8">
<title>Larkhollow Funds – Property Calculator</title>
<link href="https://fonts.googleapis.com/css2?family=Roboto:wght@400;500;700&display=swap" rel="stylesheet">
<style>
:root{
  --page-bg:#0c4c9e;
  --panel-bg:#e8e8e8;
  --white:#ffffff;
  --primary:#0455a3;
  --primary-dark:#0a3f8f;
  --accent:#3176b5;
  --sky:#86cae7;
  --link:#2196f3;
  --grey-line:#c8c8c8;
  --text:#333333;
  --text-soft:#666666;
  --green:#4caf50;
  --orange:#f57c00;
}
*{box-sizing:border-box;margin:0;padding:0}
html,body{width:1200px;height:4342px;overflow:hidden}
body{background:var(--page-bg);font-family:'Roboto',sans-serif;color:var(--text);position:relative}
.brand{position:absolute;top:72px;left:0;width:1200px;text-align:center;color:var(--white);font-weight:700;font-size:30px;letter-spacing:.5px}
.panel{position:absolute;left:42px;width:1116px;background:var(--panel-bg)}
.stepper{position:absolute;left:0;top:0;width:900px;height:190px}
.step{position:absolute;top:39px;width:74px;height:74px}
.step .disc{width:74px;height:74px;border-radius:50%;background:var(--primary);display:flex;align-items:center;justify-content:center}
.step .disc svg{width:34px;height:34px;fill:var(--white)}
.step .badge{position:absolute;left:56px;top:-6px;width:22px;height:22px;border-radius:50%;background:var(--white);border:2px solid var(--primary);color:var(--primary);font-size:12px;font-weight:700;display:flex;align-items:center;justify-content:center}
.step.current .badge{background:var(--link);border-color:var(--white);color:var(--white)}
.step .label{position:absolute;top:84px;left:-50px;width:174px;text-align:center;font-size:14px;font-weight:700;line-height:19px;text-transform:uppercase;color:#222}
.connector{position:absolute;top:74px;height:4px;background:var(--grey-line);border:1px solid #aaa;border-radius:2px}
.connector.done{background:var(--accent);border:none;height:3px;top:75px}
.connector::before,.connector::after{content:"";position:absolute;top:-4px;width:9px;height:9px;border-radius:50%;background:var(--white);border:2px solid #aaa}
.connector.done::before,.connector.done::after{border-color:var(--accent)}
.connector::before{left:-6px}.connector::after{right:-6px}
.divider{position:absolute;left:903px;top:30px;width:1px;height:120px;background:var(--grey-line)}
.btn{position:absolute;left:937px;width:120px;height:38px;font-size:14px;font-weight:700;display:flex;align-items:center;justify-content:center;letter-spacing:.3px}
.btn-prev{top:44px;background:var(--white);border:1px solid var(--grey-line);color:#333}
.btn-next{top:93px;background:var(--primary);color:var(--white)}
.content{position:absolute;left:57px;top:199px;width:1003px;background:var(--white)}
.heading{position:absolute;left:0;width:100%;text-align:center;font-size:24px;font-weight:500;color:#222}
/* panel 1 */
.type-card{position:absolute;top:180px;width:271px;height:221px;background:var(--primary);color:var(--white);text-align:center}
.type-card .pic{width:100px;height:100px;border-radius:50%;background:var(--white);margin:38px auto 0;display:flex;align-items:center;justify-content:center}
.type-card .pic span{width:56px;height:56px;border-radius:10px;background:linear-gradient(#e9a24a,#c8553d)}
.type-card .name{font-size:25px;font-weight:500;margin-top:12px}
/* panel 2 */
.map{position:absolute;left:46px;top:124px;width:360px;height:340px;background:linear-gradient(135deg,#3a8fe6,#1565c0);border-radius:46% 40% 48% 38% / 38% 50% 44% 52%}
.slider-box{position:absolute;left:454px;top:119px;width:502px;height:238px;background:#f3f3f3;box-shadow:0 2px 4px rgba(0,0,0,.1)}
.field{position:absolute;left:28px;right:52px;font-size:15px;color:var(--text-soft);display:flex;justify-content:space-between}
.field b{color:#222;font-weight:500;font-size:16px}
.info{display:inline-block;width:13px;height:13px;border-radius:50%;background:#bbb;margin-left:8px;vertical-align:-1px}
.track{position:absolute;height:4px;background:#e0e0e0;border-radius:2px}
.track .fill{position:absolute;left:0;top:0;height:4px;background:var(--link);border-radius:2px}
.track .fill::after{content:"";position:absolute;right:-7px;top:-5px;width:14px;height:14px;border-radius:50%;background:var(--white);border:2px solid var(--link)}
/* panel 3 */
.method-card{position:absolute;top:133px;width:246px;height:278px;background:#f7f7f7;box-shadow:0 3px 6px rgba(0,0,0,.15);text-align:center}
.method-card .pic{width:98px;height:98px;border-radius:50%;background:var(--white);box-shadow:0 2px 5px rgba(0,0,0,.15);margin:30px auto 0;display:flex;align-items:center;justify-content:center}
.method-card .pic span{width:54px;height:54px;border-radius:50%}
.method-card h3{font-size:19px;font-weight:500;color:#333;margin-top:20px}
.method-card p{font-size:14px;line-height:20px;color:var(--text-soft);margin:8px 30px 0}
/* panel 4 */
.row-label{position:absolute;right:519px;text-align:right;font-size:14px;line-height:20px;color:#444}
.select{position:absolute;height:45px;border:1px solid var(--grey-line);background:var(--white);font-size:14px;color:#444;padding:0 18px;display:flex;align-items:center;justify-content:space-between}
.select::after{content:"";width:6px;height:6px;border-right:1.5px solid #555;border-bottom:1.5px solid #555;transform:rotate(45deg);margin-top:-4px}
.chart-box{position:absolute;left:149px;top:273px;width:704px;height:293px;border:1px solid #e3e3e3}
/* panel 5 */
.mini-chart{position:absolute;left:542px;width:415px;height:137px}
.results{position:absolute;left:45px;top:376px;width:910px;height:83px;background:var(--primary-dark);display:flex;color:var(--white)}
.results div{flex:1;display:flex;flex-direction:column;justify-content:center;align-items:center;font-size:15px;line-height:24px;border-right:1px solid rgba(255,255,255,.25)}
.results div:last-child{border-right:none}
.results strong{font-weight:700;font-size:15px}
.note{position:absolute;left:45px;top:477px;width:910px;height:59px;border:1px solid #ddd;background:#f7f7f7;font-size:12px;line-height:19px;color:#555;padding:10px 22px}
.advanced{position:absolute;left:45px;top:556px;width:910px;height:44px;border:1px solid #ddd;box-shadow:0 1px 3px rgba(0,0,0,.1);font-size:12px;color:#555;padding:0 18px;display:flex;align-items:center}
.chart-text{font-family:'Roboto',sans-serif}
</style>
</head>
<body>
<svg width="0" height="0" style="position:absolute">
  <defs>
    <symbol id="i-home" viewBox="0 0 24 24"><path d="M12 3 2 12h3v8h5v-5h4v5h5v-8h3z"/></symbol>
    <symbol id="i-map" viewBox="0 0 24 24"><path d="M3 6l5-2 8 3 5-2v13l-5 2-8-3-5 2z" opacity=".55"/><path d="M12 5a4 4 0 0 0-4 4c0 3 4 8 4 8s4-5 4-8a4 4 0 0 0-4-4zm0 5.5a1.5 1.5 0 1 1 0-3 1.5 1.5 0 0 1 0 3z"/></symbol>
    <symbol id="i-plane" viewBox="0 0 24 24"><path d="M22 2 2 10l7 3 2 8 3-5 5 4z"/></symbol>
    <symbol id="i-chart" viewBox="0 0 24 24"><path d="M3 3h2v16h16v2H3z"/><path d="M6 15l4-5 3 3 5-6 2 2-7 8-3-3-3 3z"/></symbol>
    <symbol id="i-calc" viewBox="0 0 24 24"><path d="M5 2h14v20H5zm2 2v4h10V4zm0 7v2h2v-2zm4 0v2h2v-2zm4 0v2h2v-2zm-8 4v2h2v-2zm4 0v2h2v-2zm4 0v6h2v-6zm-8 4v2h2v-2zm4 0v2h2v-2z" fill-rule="evenodd"/></symbol>
  </defs>
</svg>

<div class="brand">Larkhollow Funds</div>

<!-- Step 1: property type -->
<section class="panel" style="top:177px;height:724px">
  <div class="stepper">
    <div class="step current" style="left:57px"><div class="disc"><svg><use href="#i-home"/></svg></div><span class="badge">1</span><div class="label">Property<br>Type</div></div>
    <div class="connector done" style="left:141px;width:87px"></div>
    <div class="step" style="left:238px"><div class="disc"><svg><use href="#i-map"/></svg></div><span class="badge">2</span><div class="label">Property<br>Location</div></div>
    <div class="connector" style="left:322px;width:84px"></div>
    <div class="step" style="left:416px"><div class="disc"><svg><use href="#i-plane"/></svg></div><span class="badge">3</span><div class="label">Property<br>Valuation</div></div>
    <div class="connector" style="left:500px;width:87px"></div>
    <div class="step" style="left:597px"><div class="disc"><svg><use href="#i-chart"/></svg></div><span class="badge">4</span><div class="label">Your Property<br>Forecast</div></div>
    <div class="connector" style="left:681px;width:86px"></div>
    <div class="step" style="left:777px"><div class="disc"><svg><use href="#i-calc"/></svg></div><span class="badge">5</span><div class="label">Calculation</div></div>
  </div>
  <div class="divider"></div>
  <div class="btn btn-prev">« PREVIOUS</div>
  <div class="btn btn-next">NEXT »</div>
  <div class="content" style="height:501px">
    <h2 class="heading" style="top:95px">What Type Of Property Would You Like To Compare?</h2>
    <div class="type-card" style="left:218px"><div class="pic" role="img" aria-label="Illustration of an apartment building"><span></span></div><div class="name">Unit</div></div>
    <div class="type-card" style="left:513px"><div class="pic" role="img" aria-label="Illustration of a house"><span></span></div><div class="name">House</div></div>
  </div>
</section>

<!-- Step 2: location -->
<section class="panel" style="top:937px;height:724px">
  <div class="stepper">
    <div class="step" style="left:57px"><div class="disc"><svg><use href="#i-home"/></svg></div><span class="badge">1</span><div class="label">Property<br>Type</div></div>
    <div class="connector done" style="left:141px;width:87px"></div>
    <div class="step current" style="left:238px"><div class="disc"><svg><use href="#i-map"/></svg></div><span class="badge">2</span><div class="label">Property<br>Location</div></div>
    <div class="connector done" style="left:322px;width:84px"></div>
    <div class="step" style="left:416px"><div class="disc"><svg><use href="#i-plane"/></svg></div><span class="badge">3</span><div class="label">Property<br>Valuation</div></div>
    <div class="connector" style="left:500px;width:87px"></div>
    <div class="step" style="left:597px"><div class="disc"><svg><use href="#i-chart"/></svg></div><span class="badge">4</span><div class="label">Your Property<br>Forecast</div></div>
    <div class="connector" style="left:681px;width:86px"></div>
    <div class="step" style="left:777px"><div class="disc"><svg><use href="#i-calc"/></svg></div><span class="badge">5</span><div class="label">Calculation</div></div>
  </div>
  <div class="divider"></div>
  <div class="btn btn-prev">« PREVIOUS</div>
  <div class="btn btn-next">NEXT »</div>
  <div class="content" style="height:501px">
    <h2 class="heading" style="top:48px">Where would this property be located?</h2>
    <div class="map" role="img" aria-label="Clickable map of Australia divided into states"></div>
    <div class="slider-box">
      <div class="field" style="top:38px"><span>How much will the property cost?<i class="info"></i></span><b>$500,000</b></div>
      <div class="track" style="left:29px;top:87px;width:421px"><div class="fill" style="width:121px"></div></div>
      <div class="field" style="top:134px"><span>How much will you invest?<i class="info"></i></span><b>$200,000</b></div>
      <div class="track" style="left:29px;top:183px;width:421px"><div class="fill" style="width:81px"></div></div>
    </div>
  </div>
</section>

<!-- Step 3: valuation -->
<section class="panel" style="top:1697px;height:724px">
  <div class="stepper">
    <div class="step" style="left:57px"><div class="disc"><svg><use href="#i-home"/></svg></div><span class="badge">1</span><div class="label">Property<br>Type</div></div>
    <div class="connector done" style="left:141px;width:87px"></div>
    <div class="step" style="left:238px"><div class="disc"><svg><use href="#i-map"/></svg></div><span class="badge">2</span><div class="label">Property<br>Location</div></div>
    <div class="connector done" style="left:322px;width:84px"></div>
    <div class="step current" style="left:416px"><div class="disc"><svg><use href="#i-plane"/></svg></div><span class="badge">3</span><div class="label">Property<br>Valuation</div></div>
    <div class="connector done" style="left:500px;width:87px"></div>
    <div class="step" style="left:597px"><div class="disc"><svg><use href="#i-chart"/></svg></div><span class="badge">4</span><div class="label">Your Property<br>Forecast</div></div>
    <div class="connector" style="left:681px;width:86px"></div>
    <div class="step" style="left:777px"><div class="disc"><svg><use href="#i-calc"/></svg></div><span class="badge">5</span><div class="label">Calculation</div></div>
  </div>
  <div class="divider"></div>
  <div class="btn btn-prev">« PREVIOUS</div>
  <div class="btn btn-next">NEXT »</div>
  <div class="content" style="height:501px">
    <h2 class="heading" style="top:63px">How would you like to forecast the returns from property?</h2>
    <div class="method-card" style="left:98px"><div class="pic" role="img" aria-label="Illustration of balance scales"><span style="background:linear-gradient(#f2b84b,#c98a2a)"></span></div><h3>Relative Cost</h3><p>Use this to value property based on mortgage cost relative to rent cost</p></div>
    <div class="method-card" style="left:377px"><div class="pic" role="img" aria-label="Illustration of a worker with coins"><span style="background:linear-gradient(#6aa8d8,#3d8a4a)"></span></div><h3>Relative to Wages</h3><p>Use this to value property based on mortgage cost relative to wages</p></div>
    <div class="method-card" style="left:657px"><div class="pic" role="img" aria-label="Percentage badge"><span style="background:linear-gradient(#f06d8a,#d9385c)"></span></div><h3>Using Rental Yield</h3><p>Use this to value property based on a rental yield</p></div>
  </div>
</section>

<!-- Step 4: forecast -->
<section class="panel" style="top:2482px;height:843px">
  <div class="stepper">
    <div class="step" style="left:57px"><div class="disc"><svg><use href="#i-home"/></svg></div><span class="badge">1</span><div class="label">Property<br>Type</div></div>
    <div class="connector done" style="left:141px;width:87px"></div>
    <div class="step" style="left:238px"><div class="disc"><svg><use href="#i-map"/></svg></div><span class="badge">2</span><div class="label">Property<br>Location</div></div>
    <div class="connector done" style="left:322px;width:84px"></div>
    <div class="step" style="left:416px"><div class="disc"><svg><use href="#i-plane"/></svg></div><span class="badge">3</span><div class="label">Property<br>Valuation</div></div>
    <div class="connector done" style="left:500px;width:87px"></div>
    <div class="step current" style="left:597px"><div class="disc"><svg><use href="#i-chart"/></svg></div><span class="badge">4</span><div class="label">Your Property<br>Forecast</div></div>
    <div class="connector" style="left:681px;width:86px"></div>
    <div class="step" style="left:777px"><div class="disc"><svg><use href="#i-calc"/></svg></div><span class="badge">5</span><div class="label">Calculation</div></div>
  </div>
  <div class="divider"></div>
  <div class="btn btn-prev">« PREVIOUS</div>
  <div class="btn btn-next">NEXT »</div>
  <div class="content" style="height:620px">
    <h2 class="heading" style="top:55px">Your Property Price Forecast</h2>
    <div class="row-label" style="top:125px">You have chosen to forecast property prices using</div>
    <div class="select" style="left:501px;top:113px;width:332px">Gross Rental Yield</div>
    <div class="row-label" style="top:187px">You can see how this ratio has changed over time<br>(in blue) below vs your assumption (in red) for</div>
    <div class="select" style="left:501px;top:185px;width:332px">Sydney House</div>
    <div class="chart-box">
      <svg width="702" height="291" viewBox="0 0 418 174" class="chart-text">
        <rect x="0" y="0" width="418" height="18" fill="#f5f9fd"/>
        <text x="209" y="13" text-anchor="middle" font-size="6.5" font-weight="500" fill="#2a7fd4">- Gross Rental Yield - Forecast</text>
        <g stroke="#e2e2e2" stroke-width=".6">
          <line x1="36" y1="55" x2="403" y2="55"/><line x1="36" y1="71" x2="403" y2="71"/><line x1="36" y1="87" x2="403" y2="87"/><line x1="36" y1="103" x2="403" y2="103"/><line x1="36" y1="119" x2="403" y2="119"/><line x1="36" y1="134" x2="403" y2="134"/>
          <line x1="36" y1="55" x2="36" y2="134"/><line x1="72" y1="55" x2="72" y2="134"/><line x1="108" y1="55" x2="108" y2="134"/><line x1="144" y1="55" x2="144" y2="134"/><line x1="180" y1="55" x2="180" y2="134"/><line x1="216" y1="55" x2="216" y2="134"/><line x1="252" y1="55" x2="252" y2="134"/><line x1="288" y1="55" x2="288" y2="134"/><line x1="324" y1="55" x2="324" y2="134"/><line x1="360" y1="55" x2="360" y2="134"/><line x1="403" y1="55" x2="403" y2="134"/>
        </g>
        <g font-size="5.5" fill="#555" text-anchor="end">
          <text x="28" y="38">30</text><text x="28" y="54">25</text><text x="28" y="70">20</text><text x="28" y="86">15</text><text x="28" y="102">10</text><text x="28" y="119">5</text><text x="28" y="135">0</text>
        </g>
        <g font-size="5.5" fill="#555" text-anchor="middle">
          <text x="62" y="157">1985</text><text x="99" y="157">1990</text><text x="136" y="157">1995</text><text x="172" y="157">2000</text><text x="208" y="157">2005</text><text x="245" y="157">2010</text><text x="281" y="157">2015</text><text x="318" y="157">2020</text><text x="355" y="157">2025</text><text x="391" y="157">2030</text>
        </g>
        <polyline points="39,100 101,82 153,110 206,119 256,105 300,117" fill="none" stroke="#2196f3" stroke-width="1.4"/>
        <line x1="300" y1="117" x2="403" y2="117" stroke="#0d47a1" stroke-width="1.4"/>
        <g fill="#2196f3" stroke="#fff" stroke-width=".8">
          <circle cx="39" cy="100" r="2.3"/><circle cx="101" cy="82" r="2.3"/><circle cx="153" cy="110" r="2.3"/><circle cx="206" cy="119" r="2.3"/><circle cx="256" cy="105" r="2.3"/><circle cx="300" cy="117" r="2.3" fill="#0d47a1"/>
        </g>
      </svg>
    </div>
  </div>
</section>

<!-- Step 5: calculation -->
<section class="panel" style="top:3370px;height:876px">
  <div class="stepper">
    <div class="step" style="left:57px"><div class="disc"><svg><use href="#i-home"/></svg></div><span class="badge">1</span><div class="label">Property<br>Type</div></div>
    <div class="connector done" style="left:141px;width:87px"></div>
    <div class="step" style="left:238px"><div class="disc"><svg><use href="#i-map"/></svg></div><span class="badge">2</span><div class="label">Property<br>Location</div></div>
    <div class="connector done" style="left:322px;width:84px"></div>
    <div class="step" style="left:416px"><div class="disc"><svg><use href="#i-plane"/></svg></div><span class="badge">3</span><div class="label">Property<br>Valuation</div></div>
    <div class="connector done" style="left:500px;width:87px"></div>
    <div class="step" style="left:597px"><div class="disc"><svg><use href="#i-chart"/></svg></div><span class="badge">4</span><div class="label">Your Property<br>Forecast</div></div>
    <div class="connector" style="left:681px;width:86px"></div>
    <div class="step current" style="left:777px"><div class="disc"><svg><use href="#i-calc"/></svg></div><span class="badge">5</span><div class="label">Calculation</div></div>
  </div>
  <div class="divider"></div>
  <div class="btn btn-prev">« PREVIOUS</div>
  <div class="btn btn-next">NEXT »</div>
  <div class="content" style="height:653px">
    <div class="row-label" style="top:74px;right:833px">Choose Property:</div>
    <div class="select" style="left:184px;top:62px;width:287px">Sydney House</div>
    <div class="row-label" style="top:128px;right:833px">Choose Alternative<br>Investment:</div>
    <div class="select" style="left:184px;top:126px;width:287px">Global Shares</div>
    <div class="field" style="top:196px;left:44px;right:532px"><span>How much will the property cost?<i class="info"></i></span><b>$500,000</b></div>
    <div class="track" style="left:45px;top:234px;width:425px"><div class="fill" style="width:81px"></div></div>
    <div class="field" style="top:263px;left:44px;right:532px"><span>How much will you invest?<i class="info"></i></span><b>$200,000</b></div>
    <div class="track" style="left:45px;top:303px;width:425px"><div class="fill" style="width:57px"></div></div>

    <svg class="mini-chart chart-text" style="top:52px" viewBox="0 0 246 81">
      <defs><linearGradient id="g-green" x1="0" y1="0" x2="0" y2="1"><stop offset="0" stop-color="#4fb553"/><stop offset="1" stop-color="#3e9a44"/></linearGradient></defs>
      <rect width="246" height="81" fill="url(#g-green)"/>
      <g stroke="rgba(255,255,255,.25)" stroke-width=".5"><line x1="24" y1="14" x2="236" y2="14"/><line x1="24" y1="31" x2="236" y2="31"/><line x1="24" y1="48" x2="236" y2="48"/><line x1="24" y1="62" x2="236" y2="62"/></g>
      <g font-size="5" fill="#fff"><text x="14" y="10">200K</text><text x="14" y="27">100K</text><text x="14" y="61">-100K</text></g>
      <g font-size="5" fill="#fff" text-anchor="middle"><text x="37" y="71">2019</text><text x="65" y="71">2021</text><text x="97" y="71">2023</text><text x="132" y="71">2025</text><text x="163" y="71">2027</text><text x="194" y="71">2028</text><text x="222" y="71">2029</text></g>
      <polyline points="24,49 52,40 85,52 117,39 149,33 182,42 214,15" fill="none" stroke="#fff" stroke-width=".9"/>
      <g fill="#fff"><circle cx="24" cy="49" r="1.3"/><circle cx="52" cy="40" r="1.3"/><circle cx="85" cy="52" r="1.3"/><circle cx="117" cy="39" r="1.3"/><circle cx="149" cy="33" r="1.3"/><circle cx="182" cy="42" r="1.3"/><circle cx="214" cy="15" r="1.3"/></g>
    </svg>

    <svg class="mini-chart chart-text" style="top:204px" viewBox="0 0 246 81">
      <defs><linearGradient id="g-orange" x1="0" y1="0" x2="0" y2="1"><stop offset="0" stop-color="#fb8c1c"/><stop offset="1" stop-color="#ef6c00"/></linearGradient></defs>
      <rect width="246" height="81" fill="url(#g-orange)"/>
      <g stroke="rgba(255,255,255,.25)" stroke-width=".5"><line x1="26" y1="13" x2="236" y2="13"/><line x1="26" y1="29" x2="236" y2="29"/><line x1="26" y1="45" x2="236" y2="45"/><line x1="26" y1="60" x2="236" y2="60"/></g>
      <g font-size="5" fill="#fff"><text x="14" y="13">10K</text><text x="20" y="30">0</text><text x="14" y="46">-10K</text><text x="14" y="62">-20K</text></g>
      <g fill="rgba(255,255,255,.85)">
        <rect x="42" y="40" width="4" height="20"/><rect x="55" y="32" width="4" height="28"/><rect x="69" y="44" width="4" height="16"/><rect x="90" y="22" width="4" height="38"/><rect x="107" y="34" width="4" height="26"/><rect x="122" y="42" width="4" height="18"/><rect x="137" y="30" width="4" height="30"/><rect x="152" y="46" width="4" height="14"/><rect x="166" y="38" width="4" height="22"/><rect x="186" y="30" width="4" height="30"/><rect x="203" y="26" width="4" height="34"/><rect x="224" y="20" width="4" height="40"/>
      </g>
      <g font-size="5" fill="#fff" text-anchor="middle"><text x="37" y="73">2019</text><text x="65" y="73">2021</text><text x="97" y="73">2023</text><text x="132" y="73">2025</text><text x="163" y="73">2027</text><text x="194" y="73">2028</text><text x="222" y="73">2029</text></g>
    </svg>

    <div class="results">
      <div><strong>AFTER 5 YEARS:</strong><span>Shares will return $82,431 more</span></div>
      <div><strong>AFTER 10 YEARS:</strong><span>Shares will return $160,176 more</span></div>
      <div><strong>DEBT CONTRIBUTION</strong></div>
    </div>
    <div class="note">Note: These are indicative figures based on a broad range of assumptions (below). Please contact Larkhollow Funds or a financial planner before making any investment based on the assumptions from this calculator.</div>
    <div class="advanced">&lt;&nbsp;&nbsp;Advanced Options</div>
  </div>
</section>
</body>
</html>
```